We (R. T. Galvin & Partners, Inc.) are an executive Search firm based in Los Angeles that is exclusively focused in the Med Tech and Health Tech arenas.   I need a logo to communicate that we are a high end search firm, but also that we are focused in the medicine and science arenas called health tech and med tech.  Many of our clients have robotics and artificial intelligence type products, so it is very technology forward.  I tend to gravitate towards clean, sharp aesthetic as opposed to something that is really over the top.
Attached are files with my logo in two different layouts.  In addition to the letterhead and envelope, I also will need an electronic letterhead in Microsoft Word.  I tend to
I look forward to seeing the designs and just let me know if you have any questions.
Dale

```html
<!DOCTYPE html>
<html lang="en">
<head>
<meta charset="utf-8">
<title>R. T. Galvin &amp; Partners, Inc. — Stationery</title>
<link rel="stylesheet" href="https://fonts.googleapis.com/css2?family=Lato:wght@400;700&family=Arimo:wght@400&display=swap">
<style>
  :root {
    --brand-blue: #3d8fd1;
    --ink: #1f1f1f;
    --text: #3a3a3a;
    --paper: #ffffff;
    --band: #0b0b0b;
    --card-dark: #232323;
    --backdrop: #e8e5e1;
  }
  * { box-sizing: border-box; margin: 0; padding: 0; }
  html, body { width: 1200px; height: 824px; overflow: hidden; }
  body { background: var(--backdrop); position: relative; font-family: "Lato", sans-serif; color: var(--text); }

  .sheet { position: absolute; background: var(--paper); box-shadow: 0 2px 8px rgba(0,0,0,.18); overflow: hidden; }

  /* Wordmark: the full name in one line, one weight, one colour, one plain square */
  .wordmark { position: absolute; display: flex; align-items: center; gap: 8px; font-family: "Lato", sans-serif; font-weight: 700; color: var(--ink); white-space: nowrap; }
  .wordmark__square { width: 12px; height: 12px; background: var(--brand-blue); flex: none; }
  .wordmark__name { font-size: 15px; line-height: 1; letter-spacing: .3px; }
  .wordmark--light { color: #ffffff; }
  .wordmark--light .wordmark__square { background: #ffffff; }

  .contact { font-family: "Arimo", sans-serif; color: #222; font-style: normal; }
  .contact__row { display: flex; align-items: center; gap: 5px; }
  .contact__icon { width: 8px; height: 8px; flex: none; }

  /* Footer: straight black strip under a thin blue rule */
  .footer-strip { position: absolute; left: 0; bottom: 0; width: 100%; background: var(--band); border-top: 3px solid var(--brand-blue); display: flex; align-items: center; justify-content: flex-end; }
  .footer-url { color: #fff; font-family: "Arimo", sans-serif; letter-spacing: 1px; }

  /* Letterhead */
  .letterhead { left: 23px; top: 49px; width: 571px; height: 738px; }
  .letterhead .wordmark { left: 40px; top: 48px; }
  .letterhead__contact { position: absolute; left: 402px; top: 27px; padding-left: 14px; border-left: 1px solid #bbb; font-size: 9.4px; line-height: 10.6px; }
  .letterhead__contact .contact__address { margin-top: 2px; }
  .letter { position: absolute; left: 60px; top: 173px; width: 450px; font-size: 8.9px; line-height: 12.3px; color: var(--text); }
  .letter__date { margin-bottom: 16px; }
  .letter__recipient { margin-bottom: 24px; }
  .letter__recipient strong { font-weight: 700; color: #111; }
  .letter__greeting { margin-bottom: 12px; }
  .letter__body p { text-align: justify; margin-bottom: 12.5px; }
  .letter__closing { margin-top: 32px; }
  .letter__signature { width: 125px; height: 20px; margin-top: 2px; background: linear-gradient(90deg, #d9d9d9, #ececec); border-radius: 3px; }
  .letterhead .footer-strip { height: 30px; padding-right: 48px; }
  .letterhead .footer-url { font-size: 9.5px; }

  /* Business cards */
  .card { width: 235px; height: 133px; }
  .card--front { left: 672px; top: 102px; background: var(--card-dark); }
  .card--front .wordmark { left: 34px; top: 59px; }
  .card--front .wordmark__name { font-size: 13px; }
  .card--front .wordmark__square { width: 10px; height: 10px; }

  .card--back { left: 672px; top: 294px; }
  .card--back .wordmark { left: 12px; top: 42px; flex-direction: column; gap: 6px; }
  .card--back .wordmark__square { width: 10px; height: 10px; }
  .card--back .wordmark__name { font-size: 8.6px; letter-spacing: .1px; }
  .card__details { position: absolute; left: 118px; top: 30px; padding-left: 7px; border-left: 1px solid #ccc; font-size: 5.2px; line-height: 6.4px; }
  .card__name { color: var(--brand-blue); font-family: "Lato", sans-serif; font-weight: 700; font-size: 7.4px; line-height: 8px; }
  .card__title { font-size: 5.2px; margin-bottom: 6px; }
  .card__address { margin-bottom: 5px; }
  .card--back .contact__icon { width: 5px; height: 5px; }
  .card--back .contact__row { gap: 3px; }
  .card--back .footer-strip { height: 14px; padding-right: 16px; border-top-width: 2px; }
  .card--back .footer-url { font-size: 5.6px; letter-spacing: .6px; }

  /* Envelope */
  .envelope { left: 622px; top: 499px; width: 554px; height: 261px; }
  .envelope .wordmark { left: 34px; top: 50px; }
  .envelope__contact { position: absolute; left: 33px; top: 163px; font-size: 8.8px; line-height: 10.6px; }
  .envelope__contact .contact__address { margin-top: 5px; }
  .envelope .footer-strip { height: 26px; padding-right: 32px; }
  .envelope .footer-url { font-size: 8.6px; }
</style>
</head>
<body>

<section class="sheet letterhead" aria-label="Letterhead">
  <div class="wordmark">
    <span class="wordmark__square"></span>
    <span class="wordmark__name">R. T. Galvin &amp; Partners, Inc.</span>
  </div>

  <address class="contact letterhead__contact">
    <div class="contact__row">
      <svg class="contact__icon" viewBox="0 0 10 10"><path d="M2 1h2l1 2.5-1.3 1a6 6 0 0 0 2.8 2.8l1-1.3L10 7v2c0 .6-.4 1-1 1A9 9 0 0 1 0 1c0-.6.4-1 1-1z" fill="var(--brand-blue)"/></svg>
      +1.310.555.0142
    </div>
    <div class="contact__row">
      <svg class="contact__icon" viewBox="0 0 10 10"><rect x="2.5" y="0.5" width="5" height="3" fill="var(--brand-blue)"/><rect x="0.5" y="3.5" width="9" height="4.5" rx="1" fill="var(--brand-blue)"/><rect x="2.5" y="6.5" width="5" height="3" fill="#fff" stroke="var(--brand-blue)"/></svg>
      +1.310.555.0143
    </div>
    <div class="contact__row">
      <svg class="contact__icon" viewBox="0 0 10 10"><rect x="0.5" y="1.5" width="9" height="7" fill="var(--brand-blue)"/><path d="M0.5 1.5 5 5.5l4.5-4" fill="none" stroke="#fff" stroke-width="1"/></svg>
      info@rtgpinc.com
    </div>
    <div class="contact__address">2200 Ocean Park Blvd<br>Suite #410<br>Santa Monica CA 90405</div>
  </address>

  <article class="letter">
    <p class="letter__date">01 January 2050</p>
    <p class="letter__recipient"><strong>Company (Pvt) Ltd.</strong><br>PO Box 3355 Mainville St<br>Sample City Country 3355</p>
    <p class="letter__greeting">Dear Alan Whitcombe,</p>
    <div class="letter__body">
      <p>Dolor sit amet, consectetuer adipiscing elit, sed diam nonummy nibh euismod tincidunt ut laoreet dolore magna aliquam erat volutpat. Ut wisi enim ad minim veniam, quis nostrud exerci tation ullamcorper suscipit lobortis nisl ut aliquip ex ea commodo consequat. Duis dolore te feugait nulla facilisi. Nam liber tempor cum soluta nobis eleifend option congue nihil imperdiet doming id quod mazim placerat facer possim assum. Lorem ipsum dolor sit amet, consectetuer adipiscing elit, sed diam nonummy nibh euismod tincidunt ut laoreet dolore magna aliquam erat volutpat. Ut wisi enim ad minim veniam, quis nostrud exerci tation ullamcorper suscipit lobortis nisl ut aliquip ex ea commodo consequat.</p>
      <p>Consectetuer adipiscing elit, sed diam nonummy nibh euismod tincidunt ut laoreet dolore magna aliquam erat volutpat. Ut wisi enim ad minim veniam, quis nostrud exerci tation ullamcorper suscipit lobortis nisl ut aliquip ex ea commodo consequat. Consectetuer adipiscing elit, sed diam nonummy nibh euismod tincidunt ut laoreet dolore magna aliquam erat volutpat. Ut wisi enim ad minim veniam, quis nostrud exerci tation ullamcorper suscipit lobortis nisl ut aliquip ex ea commodo consequat.</p>
      <p>Sed diam nonummy nibh euismod tincidunt ut laoreet dolore magna aliquam erat volutpat. Ut wisi enim ad minim veniam, quis nostrud exerci tation ullamcorper suscipit lobortis nisl ut aliquip ex ea commodo consequat. Consectetuer adipiscing elit, sed diam nonummy nibh euismod tincidunt ut laoreet dolore magna aliquam erat volutpat. Ut wisi enim ad minim veniam, quis nostrud exerci tation ullamcorper suscipit lobortis nisl ut aliquip ex ea commodo consequat.</p>
    </div>
    <p class="letter__closing">Sincerely Yours</p>
    <div class="letter__signature" role="img" aria-label="Handwritten signature of Dale Galvin"></div>
  </article>

  <div class="footer-strip"><span class="footer-url">www.rtgpinc.com</span></div>
</section>

<section class="sheet card card--front" aria-label="Business card front">
  <div class="wordmark wordmark--light">
    <span class="wordmark__square"></span>
    <span class="wordmark__name">R. T. Galvin &amp; Partners, Inc.</span>
  </div>
</section>

<section class="sheet card card--back" aria-label="Business card back">
  <div class="wordmark">
    <span class="wordmark__square"></span>
    <span class="wordmark__name">R. T. Galvin &amp; Partners, Inc.</span>
  </div>
  <div class="contact card__details">
    <div class="card__name">Dale Galvin</div>
    <div class="card__title">Executive Recruiter</div>
    <div class="card__address">2200 Ocean Park Blvd<br>Suite #410<br>Santa Monica CA 90405</div>
    <div class="contact__row">
      <svg class="contact__icon" viewBox="0 0 10 10"><path d="M2 1h2l1 2.5-1.3 1a6 6 0 0 0 2.8 2.8l1-1.3L10 7v2c0 .6-.4 1-1 1A9 9 0 0 1 0 1c0-.6.4-1 1-1z" fill="var(--brand-blue)"/></svg>
      +1.310.555.0142
    </div>
    <div class="contact__row">
      <svg class="contact__icon" viewBox="0 0 10 10"><rect x="0.5" y="3" width="9" height="5" rx="1" fill="var(--brand-blue)"/><rect x="2.5" y="0.5" width="5" height="3" fill="var(--brand-blue)"/></svg>
      +1.310.555.0143
    </div>
    <div class="contact__row">
      <svg class="contact__icon" viewBox="0 0 10 10"><rect x="0.5" y="1.5" width="9" height="7" fill="var(--brand-blue)"/><path d="M0.5 1.5 5 5.5l4.5-4" fill="none" stroke="#fff"/></svg>
      info@rtgpinc.com
    </div>
  </div>
  <div class="footer-strip"><span class="footer-url">www.rtgpinc.com</span></div>
</section>

<section class="sheet envelope" aria-label="Envelope">
  <div class="wordmark">
    <span class="wordmark__square"></span>
    <span class="wordmark__name">R. T. Galvin &amp; Partners, Inc.</span>
  </div>
  <address class="contact envelope__contact">
    <div class="contact__row">
      <svg class="contact__icon" viewBox="0 0 10 10"><path d="M2 1h2l1 2.5-1.3 1a6 6 0 0 0 2.8 2.8l1-1.3L10 7v2c0 .6-.4 1-1 1A9 9 0 0 1 0 1c0-.6.4-1 1-1z" fill="var(--brand-blue)"/></svg>
      +1.310.555.0142
    </div>
    <div class="contact__row">
      <svg class="contact__icon" viewBox="0 0 10 10"><rect x="2.5" y="0.5" width="5" height="3" fill="var(--brand-blue)"/><rect x="0.5" y="3.5" width="9" height="4.5" rx="1" fill="var(--brand-blue)"/><rect x="2.5" y="6.5" width="5" height="3" fill="#fff" stroke="var(--brand-blue)"/></svg>
      +1.310.555.0143
    </div>
    <div class="contact__row">
      <svg class="contact__icon" viewBox="0 0 10 10"><rect x="0.5" y="1.5" width="9" height="7" fill="var(--brand-blue)"/><path d="M0.5 1.5 5 5.5l4.5-4" fill="none" stroke="#fff"/></svg>
      info@rtgpinc.com
    </div>
    <div class="contact__address">2200 Ocean Park Blvd<br>Suite #410, Santa Monica CA 90405</div>
  </address>
  <div class="footer-strip"><span class="footer-url">www.rtgpinc.com</span></div>
</section>

</body>
</html>
```